NEW Modern Sleek Business Card for VR Language Startup

Our startup is using VR to lead the next wave of world language education. We need a two-sided business card that introduces the larger organization (Brightloom Language Inc) and our contact info on one side and shows the product, Glimwoorld, on the other side.

Side 1 (contact info)= Brightloom Logo and Contact info (name, title, phone, email)

Side 2 (product)= Glimworld logo, text, and website
Text= Culturally Immersive Language Learning Games
Website= www.glimworld-play.com

Target Market(s)

Education, Technology

Contact Information for Business Card

Contact info will be updated upon approval of the design. For now, put this as a placeholder.

Perry Dunmore
Founder & CEO
pdunmore@quillpost-mail.net
(555)-014-2286

Font styles to use
Other font styles liked:
• Gibson and Century Gothic are the brand fonts

Requirements
Nice to have
• I would love to see cohesion between the design and colors of the two logos. I have attached a few business card designs that I like, so you can get a feel for my preferred style.

```html
<!DOCTYPE html>
<html lang="en">
<head>
<meta charset="utf-8">
<title>Brightloom Language – Business Card</title>
<link href="https://fonts.googleapis.com/css2?family=Questrial&family=Montserrat:wght@600;700&display=swap" rel="stylesheet">
<style>
  :root {
    --page-bg: #dcdcdd;
    --card-bg: #efeff0;
    --ink: #1d1d1f;
    --ink-soft: #4a4a4d;
    --muted: #8a8a8e;
    --accent-yellow: #e9b52a;
    --accent-orange: #ec5a2c;
    --accent-magenta: #b43fae;
    --accent-blue: #5a4df0;
    --accent-teal: #19e0c8;
  }
  * { box-sizing: border-box; margin: 0; padding: 0; }
  html, body { width: 1200px; height: 1200px; overflow: hidden; }
  body {
    background: radial-gradient(circle at 50% 30%, #e6e6e7 0%, var(--page-bg) 70%);
    font-family: "Questrial", "Century Gothic", sans-serif;
    color: var(--ink);
    position: relative;
  }
  .card {
    position: absolute;
    width: 640px;
    height: 366px;
    background: var(--card-bg);
    border-radius: 26px;
    box-shadow: 0 3px 0 #cfcfd1, 0 18px 34px rgba(0,0,0,0.16);
    overflow: hidden;
  }
  .card--front { left: 110px; top: 170px; }
  .card--back { left: 450px; top: 650px; }

  .brand-accent {
    position: absolute;
    right: 0;
    top: 0;
    width: 210px;
    height: 250px;
    border-bottom-left-radius: 120px;
    background: linear-gradient(160deg, var(--accent-yellow) 0%, var(--accent-orange) 28%, var(--accent-magenta) 52%, var(--accent-blue) 74%, var(--accent-teal) 100%);
  }

  .wordmark {
    display: flex;
    align-items: center;
    gap: 14px;
  }
  .wordmark__dot {
    width: 46px;
    height: 46px;
    border-radius: 50%;
    background: var(--accent-magenta);
    flex: none;
  }
  .wordmark__name {
    font-family: "Montserrat", "Century Gothic", sans-serif;
    font-weight: 700;
    color: var(--ink);
    text-transform: uppercase;
    line-height: 1.05;
  }
  .wordmark__main { display: block; font-size: 27px; letter-spacing: 4px; }
  .wordmark__sub { display: block; font-size: 12px; letter-spacing: 9px; margin-top: 3px; }

  .front-content {
    position: absolute;
    left: 70px;
    top: 130px;
  }
  .contact { margin-top: 20px; padding-left: 60px; }
  .contact__name { font-size: 28px; color: var(--ink-soft); line-height: 1; }
  .contact__title { font-size: 11px; color: var(--ink-soft); margin-top: 4px; }
  .contact__line { font-size: 16px; color: var(--ink-soft); margin-top: 10px; line-height: 1.2; }
  .contact__line + .contact__line { margin-top: 4px; }

  .back-content {
    position: absolute;
    inset: 0;
    display: flex;
    flex-direction: column;
    align-items: center;
    justify-content: center;
    text-align: center;
  }
  .wordmark--product .wordmark__main { font-size: 30px; letter-spacing: 6px; }
  .tagline {
    margin-top: 24px;
    font-family: "Montserrat", "Century Gothic", sans-serif;
    font-weight: 600;
    font-size: 17px;
    color: var(--muted);
  }
  .website {
    margin-top: 16px;
    font-size: 14px;
    color: var(--muted);
    letter-spacing: 0.5px;
  }
</style>
</head>
<body>
  <section class="card card--front" aria-label="Business card front">
    <div class="brand-accent" role="img" aria-label="Large gradient brand decoration in yellow, orange, magenta, blue and teal"></div>
    <div class="front-content">
      <div class="wordmark">
        <span class="wordmark__dot"></span>
        <span class="wordmark__name">
          <span class="wordmark__main">Brightloom</span>
          <span class="wordmark__sub">Language</span>
        </span>
      </div>
      <div class="contact">
        <p class="contact__name">Perry Dunmore</p>
        <p class="contact__title">Founder &amp; CEO</p>
        <p class="contact__line">pdunmore@quillpost-mail.net</p>
        <p class="contact__line">0400 555 019</p>
      </div>
    </div>
  </section>

  <section class="card card--back" aria-label="Business card back">
    <div class="back-content">
      <div class="wordmark wordmark--product">
        <span class="wordmark__dot"></span>
        <span class="wordmark__name"><span class="wordmark__main">Glimworld</span></span>
      </div>
      <p class="tagline">Culturally Immersive Language Learning Games</p>
      <p class="website">www.glimworld-play.com</p>
    </div>
  </section>
</body>
</html>
```